Coach Bruno Velasque Life Coach webpage

I am a Triathlon Coach but now I am in the process of opening a "new brand" as a Life Coach therefore I need new image and a new webpage. I live in Mexico city and would like to offer my services to Latinamerican clientes (spanish speaking). My actual website is www.trenquo.mx. My new website should help me to communicate what I do (Life Coaching), how my services are different from others, help gain new clients through one on one sessions, and I also offer a mental training course. I would like to see designs from a ZEN perspective (minimalistic, light and peaceful colors and not strong colors like my current webpage). The final design should communicate a sense of peace, tranquility, accomplishment and accompaniment. I would like to be able to manipulate the information and add-ons such a section were people can buy, subscribe and pay for the courses.

Target Market(s)

Male and female between 35 and 60 years who are going through changes in their life, need to make important decisions (such a divorcing or not, quitting or changing jobs, or not, etc), and or who do not fell happy with their current life.

Industry/Entity Type

Coaching

Coding

Coded - Design and coding required

Number of Pages Required

5+ page

Font styles to use
Sans Serif

Colors

Designer to choose colors to be used in the design.

Requirements
Must have
• 6 sections and one of those sections a place where my clients can buy courses and pay for them there. I would like to be able to change some of the information easily. I would like to see designs from a ZEN perspective (minimalistic, light and peaceful colors and not strong colors like my current webpage). The final design should communicate a sense of peace, tranquility, accomplishment and accompaniment. I would like to be able to manipulate the informati
Should not have
• dark strong colors

```html
<!DOCTYPE html>
<html lang="en">
<head>
<meta charset="utf-8">
<title>Bruno Velasque – Life Coach</title>
<link rel="stylesheet" href="https://fonts.googleapis.com/css2?family=Cinzel:wght@400;700&family=Roboto:ital,wght@0,400;0,500;0,700;1,700&display=swap">
<style>
:root{
  --accent:#d4917a;
  --accent-deep:#c8714f;
  --accent-dark:#c17f68;
  --ink:#1c1c1c;
  --text:#555;
  --muted:#8a8a8a;
  --grey-band:#e4e4e4;
  --grey-soft:#f4f4f4;
  --white:#fff;
  --serif:'Cinzel', serif;
  --sans:'Roboto', sans-serif;
}
*{margin:0;padding:0;box-sizing:border-box}
html,body{width:1200px;height:3852px;overflow:hidden}
body{position:relative;font-family:var(--sans);color:var(--ink);background:var(--white)}
.abs{position:absolute}
a{color:inherit;text-decoration:none}

/* top bar + nav */
.topbar{left:0;top:0;width:1200px;height:31px;background:var(--accent);color:#fff;font-size:14px;text-align:center;line-height:31px}
.nav{left:0;top:31px;width:1200px;height:65px;background:#fff}
.logo{font-family:var(--serif);font-weight:700;color:var(--accent-deep);font-size:30px;letter-spacing:.5px;white-space:nowrap}
.nav .logo{left:112px;top:18px;font-size:23px;letter-spacing:0}
.menu{left:370px;top:26px;display:flex;gap:27px;font-size:13px;font-weight:500;color:#333}
.menu .active{color:var(--accent-deep)}
.btn-outline{display:inline-block;border:2px solid var(--accent);color:var(--ink);font-weight:700;font-size:13px;padding:11px 13px;border-radius:3px;background:#fff}
.nav .btn-outline{left:915px;top:10px}

/* hero */
.hero{left:0;top:96px;width:1200px;height:540px;background:linear-gradient(100deg,#f6f6f6 0%,#ececec 35%,#d7d9d8 60%,#c9cbc9 100%)}
.hero-copy{left:112px;top:227px}
.hero-copy .pre{font-family:var(--sans);font-size:25px;color:#222}
.hero-copy h1{font-family:var(--serif);font-weight:700;font-size:64px;line-height:1;margin-top:14px;color:#111;white-space:nowrap}
.hero-copy p{font-style:italic;font-weight:700;font-size:14.5px;line-height:23px;margin-top:16px;width:412px;color:#222}
.hero-copy .btn-outline{margin-top:24px;padding:10px 11px;font-size:13px}

/* feature cards */
.feature{height:99px;background:#fff;border-radius:6px;box-shadow:0 4px 18px rgba(0,0,0,.08);display:flex;align-items:center;padding-left:26px;gap:20px}
.feature h3{font-size:20px;font-weight:500}
.feature p{font-size:14px;color:var(--muted);line-height:19px;margin-top:4px}
.feature.featured{background:var(--accent);color:#fff;height:116px;box-shadow:0 6px 20px rgba(0,0,0,.12)}
.feature.featured p{color:#fff;font-weight:700}
.feature .icon-badge{width:60px;height:60px;border-radius:50%;background:#fff;display:flex;align-items:center;justify-content:center}

/* headings */
.eyebrow{font-size:12px;color:var(--accent-deep);text-transform:uppercase}
.section-title{font-family:var(--serif);font-size:37px;line-height:1.2;color:#111}
.section-title b{font-weight:700}
.section-title span{color:var(--accent);font-weight:400}
.center{text-align:center;width:1200px;left:0}

/* about */
.about-frame{left:150px;top:806px;width:406px;height:380px;border:2px solid var(--accent);border-radius:8px}
.photo{border-radius:6px}
.about-photo{left:111px;top:778px;width:393px;height:434px;background:linear-gradient(160deg,#cfc9c2,#9e958d 60%,#6f6862)}
.about-copy{left:642px;top:780px;width:445px}
.about-copy .section-title{white-space:nowrap;font-size:33px}
.about-copy p{font-size:14.5px;line-height:25.7px;color:var(--text);margin-top:26px}
.about-copy .btn-outline{margin-top:14px;padding:10px 17px}

/* split band */
.split{left:0;top:1290px;width:1200px;height:400px}
.split-col{top:1388px;width:600px;text-align:center}
.split-col h3{font-family:var(--serif);font-size:23px;font-weight:400;letter-spacing:.3px}
.split-col p{font-size:15px;line-height:25.7px;color:var(--text);margin:18px auto 0;width:430px}
.split-col .more{display:inline-block;margin-top:20px;font-size:13px;font-weight:700;text-decoration:underline}
.split-col.light h3,.split-col.light p,.split-col.light .more{color:#fff}
.split-col.light p{font-weight:500}

/* courses */
.courses-bg{left:0;top:1676px;width:1200px;height:580px;background:var(--grey-soft)}
.course{top:1822px;width:308px;height:367px;background:#fff;border-radius:4px;box-shadow:0 3px 10px rgba(0,0,0,.06);overflow:hidden}
.course .media{height:299px}
.course .label{height:68px;line-height:68px;text-align:center;font-size:15px;font-weight:700}
.course.active .label{background:var(--accent);color:#fff}
.arrow{width:34px;height:34px;border-radius:50%;display:flex;align-items:center;justify-content:center}
.arrow.prev{background:#111}
.arrow.next{border:1.5px solid #111;background:#fff}

/* faq */
.faq-copy{left:111px;top:2365px}
.faq-copy .section-title{font-size:38px;line-height:46px;margin-top:14px}
.faq-item{width:463px;height:69px;background:#fbeeea;display:flex;align-items:center;justify-content:space-between;padding:0 22px 0 19px;font-family:var(--serif);font-size:14px;font-weight:700;color:#222;margin-top:10px}
.faq-item .toggle{width:22px;height:22px;border-radius:50%;background:#111;display:flex;align-items:center;justify-content:center}
.faq-copy .list{margin-top:40px}
.faq-copy .btn-outline{margin-top:16px;padding:10px 9px}

/* blog */
.post{top:2978px;width:295px;height:422px;background:#fff;border-radius:4px;box-shadow:0 2px 12px rgba(0,0,0,.1);overflow:hidden}
.post .media{height:192px}
.post .body{padding:22px 15px 0}
.post h4{font-size:16px;font-weight:700}
.post p{font-size:14px;line-height:23.4px;color:var(--muted);margin-top:8px}
.post .more{display:inline-block;margin-top:10px;font-size:14px;font-weight:700;color:var(--accent-deep);text-decoration:underline}

/* footer */
.footer{left:0;top:3474px;width:1200px;height:378px;background:var(--accent);color:#fff}
.footer .logo{color:#fff;font-weight:400;font-size:28px;letter-spacing:0;left:111px;top:58px}
.footer .about-text{left:111px;top:108px;width:255px;font-size:14.5px;line-height:21px}
.f-head{font-family:var(--serif);font-size:19px}
.f-links{list-style:none;font-size:13px;font-weight:700;line-height:30.7px;margin-top:14px}
.divider{width:2px;background:rgba(255,255,255,.7)}
.contact-row{display:flex;gap:14px;align-items:flex-start}
.contact-row .ic{width:44px;height:44px;border-radius:50%;background:#fff;display:flex;align-items:center;justify-content:center;flex:none}
.contact-row b{display:block;font-size:15px}
.contact-row span{font-size:15px;line-height:21px}
.social{width:38px;height:38px;border-radius:50%;border:1.5px solid #fff}
.social.filled{background:#fff;opacity:.9}
.copyright{left:0;top:3808px;width:1200px;height:44px;background:var(--accent-dark);color:#fff;font-size:14px;text-align:center;line-height:44px;border-top:1px solid rgba(255,255,255,.4)}
</style>
</head>
<body>

<div class="abs topbar">Lorem ipsum dolor sit amet, consectetur</div>

<header class="abs nav">
  <div class="abs logo">BRUNO VELASQUE</div>
  <nav class="abs menu">
    <a class="active" href="#">HOME</a><a href="#">ABOUT ME</a><a href="#">SERVICES</a><a href="#">BLOG</a><a href="#">FAQS</a><a href="#">CONTACT US</a>
  </nav>
  <a class="abs btn-outline" href="#">JOIN YOUR PROGRAM</a>
</header>

<section class="abs hero" role="img" aria-label="Photo of two women talking at a bright office desk with a laptop"></section>
<div class="abs hero-copy">
  <div class="pre">WELCOME TO</div>
  <h1>BRUNO VELASQUE</h1>
  <p>LOREM IPSUM DOLOR SIT AMET, CONSECTETUR IPISCING ELIT, SED DO EIUSMOD TEMPOR .</p>
  <a class="btn-outline" href="#">GET STARTED</a>
</div>

<div class="abs feature" style="left:180px;top:585px;width:280px">
  <svg width="48" height="44" viewBox="0 0 48 44" fill="none" stroke="#222" stroke-width="2"><circle cx="22" cy="9" r="6"/><path d="M12 30v-8a10 10 0 0 1 20 0v8"/><path d="M4 30h40M8 30v12M40 30v12"/><rect x="30" y="18" width="12" height="9"/></svg>
  <div><h3>LOREM IPSUM</h3><p>Lorem ipsum dolor sitdf<br>amet, consectetur</p></div>
</div>
<div class="abs feature featured" style="left:459px;top:577px;width:281px">
  <div class="icon-badge"><svg width="40" height="36" viewBox="0 0 40 36" fill="none" stroke="#222" stroke-width="2"><circle cx="12" cy="8" r="4"/><circle cx="28" cy="8" r="4"/><path d="M5 24v-5a7 7 0 0 1 14 0v5M21 24v-5a7 7 0 0 1 14 0v5"/><path d="M2 24h36M8 24v10M32 24v10M20 24v10"/></svg></div>
  <div><h3>LOREM IPSUM</h3><p>Lorem ipsum dolor sitdf<br>amet, consectetur</p></div>
</div>
<div class="abs feature" style="left:744px;top:585px;width:276px">
  <svg width="44" height="44" viewBox="0 0 44 44" fill="none" stroke="#222" stroke-width="2"><path d="M4 4h18v11H10l-4 4v-4H4z"/><path d="M24 10h16v10h-2v4l-4-4h-6"/><circle cx="12" cy="29" r="4"/><circle cx="32" cy="29" r="4"/><path d="M5 42a7 7 0 0 1 14 0M25 42a7 7 0 0 1 14 0"/></svg>
  <div><h3>LOREM IPSUM</h3><p>Lorem ipsum dolor sitdf<br>amet, consectetur</p></div>
</div>

<!-- about -->
<div class="abs about-frame"></div>
<div class="abs photo about-photo" role="img" aria-label="Portrait photo of the coach, arms crossed, in a white shirt in an office"></div>
<div class="abs about-copy">
  <div class="eyebrow">Who we are</div>
  <h2 class="section-title" style="margin-top:4px"><b>ABOUT</b> <span>BRUNO VELASQUE</span></h2>
  <p>Lorem ipsum dolor sit amet, consectetur adipiscing elit, sed do mod tempor incididunt ut labore et dolore magna aliqua. Ut enim ad inim veniam, quis nostrud exercitation ullamco laboris nisi ut aliquip ex ea commodo consequat. Duis aute irure dolor in ehenderit in luptate velit esse cillum dolore eu fugiat nula pariatur. Excepteur sint caecat cupidatat non proident, sunt in culpa qui officia eserunt mollit anim id est laborum Lorem ipsum dolor sit amet, consectetur adipiscing elit, sed do mod tempor incididunt ut labore et dolore magna aliqua. Ut enim ad inim veniam, quis nostrud.</p>
  <a class="btn-outline" href="#">READ MORE</a>
</div>

<!-- split band -->
<div class="abs courses-bg"></div>
<svg class="abs split" viewBox="0 0 1200 400" preserveAspectRatio="none">
  <polygon points="0,0 600,30 600,388 0,386" fill="#e4e4e4"/>
  <polygon points="600,30 1200,0 1200,386 600,348" fill="#d4917a"/>
</svg>
<div class="abs split-col" style="left:0">
  <h3>PERSONALIZED LIFE COACHING</h3>
  <p>Lorem ipsum dolor sit amet, consectetur adipiscing elit, sed do mod tempor incididunt ut labore et dolore magna aliqua. Ut enim ad inim veniam, quis nostrud exercitation ullamco laboris nisi ut aliquip ex ea commodo consequat.</p>
  <a class="more" href="#">READ MORE</a>
</div>
<div class="abs split-col light" style="left:600px">
  <h3>MENTAL TRAINING COURSES</h3>
  <p>Lorem ipsum dolor sit amet, consectetur adipiscing elit, sed do mod tempor incididunt ut labore et dolore magna aliqua. Ut enim ad inim veniam, quis nostrud exercitation ullamco laboris nisi ut aliquip ex ea commodo consequat.</p>
  <a class="more" href="#">READ MORE</a>
</div>

<!-- courses -->
<div class="abs center" style="top:1718px"><div class="eyebrow">Our shop</div><h2 class="section-title" style="margin-top:8px"><b>OUR</b> <span>COURSES</span></h2></div>
<div class="abs arrow prev" style="left:44px;top:1973px"><svg width="12" height="14" viewBox="0 0 12 14"><path d="M8 2 3 7l5 5" stroke="#fff" stroke-width="2.5" fill="none"/></svg></div>
<div class="abs arrow next" style="left:1122px;top:1973px"><svg width="12" height="14" viewBox="0 0 12 14"><path d="M4 2l5 5-5 5" stroke="#111" stroke-width="2" fill="none"/></svg></div>
<div class="abs course" style="left:114px"><div class="media" role="img" aria-label="Photo of a person reading an e-reader" style="background:linear-gradient(150deg,#e6e1da,#bdb6ae 60%,#8d857d)"></div><div class="label">E-BOOKS</div></div>
<div class="abs course active" style="left:448px"><div class="media" role="img" aria-label="Photo of a woman choosing a wellness product on a shop shelf" style="background:linear-gradient(150deg,#7a5c4c,#a88f7c 50%,#dcd3c7)"></div><div class="label">WELLNESS PRODUCTS</div></div>
<div class="abs course" style="left:782px"><div class="media" role="img" aria-label="Photo of a seated audience listening to a trainer" style="background:linear-gradient(170deg,#e2e0dc,#9a948c 55%,#4a4540)"></div><div class="label">TRAINING</div></div>

<!-- faq -->
<div class="abs faq-copy">
  <div class="eyebrow">FAQ</div>
  <h2 class="section-title"><b>FREQUENTLY</b> <span>ASKED<br>QUESTIONS</span></h2>
  <div class="list">
    <div class="faq-item">WHAT ARE THE BENEFITS OF LIFE COACHING?<span class="toggle"><svg width="10" height="8" viewBox="0 0 10 8"><path d="M1 6l4-4 4 4" stroke="#fff" stroke-width="2" fill="none"/></svg></span></div>
    <div class="faq-item">HOW MANY SESSIONS DO I NEED TO SEE RESULTS?<span class="toggle"><svg width="10" height="8" viewBox="0 0 10 8"><path d="M1 6l4-4 4 4" stroke="#fff" stroke-width="2" fill="none"/></svg></span></div>
  </div>
  <a class="btn-outline" href="#">LEARN MORE</a>
</div>
<div class="abs" style="left:933px;top:2343px;width:152px;height:387px;background:var(--accent)"></div>
<div class="abs" style="left:642px;top:2386px;width:110px;height:302px;background:#c9c9c9" role="img" aria-label="Faded edge of a workshop room photo"></div>
<div class="abs photo" style="left:706px;top:2376px;width:328px;height:324px;background:linear-gradient(170deg,#f0efec,#c4c0ba 55%,#3e3a36)" role="img" aria-label="Photo of a speaker presenting to a seated group in a bright loft room"></div>

<!-- blog -->
<div class="abs center" style="top:2872px"><div class="eyebrow">Latest news</div><h2 class="section-title" style="margin-top:8px"><b>OUR LATEST</b> <span>BLOG</span></h2></div>
<div class="abs arrow prev" style="left:44px;top:3183px"><svg width="12" height="14" viewBox="0 0 12 14"><path d="M8 2 3 7l5 5" stroke="#fff" stroke-width="2.5" fill="none"/></svg></div>
<div class="abs arrow next" style="left:1122px;top:3183px"><svg width="12" height="14" viewBox="0 0 12 14"><path d="M4 2l5 5-5 5" stroke="#111" stroke-width="2" fill="none"/></svg></div>
<article class="abs post" style="left:109px"><div class="media" role="img" aria-label="Photo of business people seated in a circle" style="background:linear-gradient(160deg,#dedcda,#8c8783 55%,#3b3836)"></div><div class="body"><h4>Lorem ipsum dolor sit amet</h4><p>Lorem ipsum dolor sit amet, onsectetur adipiscing elit, sed do mod tempor dunt ut labore et dolore magna aliqua.Lorem ipsum dolor sit amet, onsectetur iscing elit, sed do mod</p><a class="more" href="#">READ MORE</a></div></article>
<article class="abs post" style="left:452px"><div class="media" role="img" aria-label="Photo of a woman speaking at a seminar" style="background:linear-gradient(160deg,#eef0f0,#c2c6c6 55%,#5b5a58)"></div><div class="body"><h4>Lorem ipsum dolor sit amet</h4><p>Lorem ipsum dolor sit amet, onsectetur adipiscing elit, sed do mod tempor dunt ut labore et dolore magna aliqua.Lorem ipsum dolor sit amet, onsectetur iscing elit, sed do mod</p><a class="more" href="#">READ MORE</a></div></article>
<article class="abs post" style="left:794px"><div class="media" role="img" aria-label="Photo of an audience at a conference talk" style="background:linear-gradient(170deg,#ecebe8,#a39e98 55%,#3f3b37)"></div><div class="body"><h4>Lorem ipsum dolor sit amet</h4><p>Lorem ipsum dolor sit amet, onsectetur adipiscing elit, sed do mod tempor dunt ut labore et dolore magna aliqua.Lorem ipsum dolor sit amet, onsectetur iscing elit, sed do mod</p><a class="more" href="#">READ MORE</a></div></article>

<!-- footer -->
<footer class="abs footer">
  <div class="abs logo">BRUNO VELASQUE</div>
  <p class="abs about-text">Lorem ipsum dolor sit amet, ctetur adipiscing elit, sed do eiusmod por incididunt ut labore et dolore magna aliqua. Quis ipsum suspendisse ces gravida. Risus commodo iverra nas accumsan lacus vel facilisis.</p>

  <div class="abs" style="left:423px;top:56px">
    <div class="f-head">QUICK LINKS</div>
    <ul class="f-links"><li>HOME</li><li>ABOUT US</li><li>SERVICES</li><li>STORE</li><li>BLOG</li><li>FAQS</li><li>CONTACT US</li></ul>
  </div>
  <div class="abs divider" style="left:595px;top:40px;height:290px"></div>

  <div class="abs" style="left:642px;top:56px">
    <div class="f-head">CONTACT US</div>
    <div class="contact-row" style="margin-top:18px"><span class="ic"><svg width="20" height="20" viewBox="0 0 24 24"><path fill="#d4917a" d="M6.6 10.8a15 15 0 0 0 6.6 6.6l2.2-2.2a1 1 0 0 1 1-.25 11.4 11.4 0 0 0 3.6.57 1 1 0 0 1 1 1V20a1 1 0 0 1-1 1A17 17 0 0 1 3 4a1 1 0 0 1 1-1h3.5a1 1 0 0 1 1 1c0 1.25.2 2.45.57 3.57a1 1 0 0 1-.25 1z"/></svg></span><div><b>PHONE NO:</b><span>+52 (55) 4120 7788</span></div></div>
    <div class="contact-row" style="margin-top:26px"><span class="ic"><svg width="20" height="16" viewBox="0 0 20 16"><rect x="1" y="1" width="18" height="14" rx="2" fill="#d4917a"/><path d="M2 3l8 6 8-6" stroke="#fff" stroke-width="1.6" fill="none"/></svg></span><div><b>EMAIL:</b><span>info@brunovelasque.mx</span></div></div>
    <div class="contact-row" style="margin-top:26px"><span class="ic"><svg width="18" height="22" viewBox="0 0 18 22"><path fill="#d4917a" d="M9 0a8 8 0 0 0-8 8c0 6 8 14 8 14s8-8 8-14a8 8 0 0 0-8-8z"/><circle cx="9" cy="8" r="3" fill="#fff"/></svg></span><div><b>LOCATION:</b><span>Lorem ipsum dolor sit<br>amet,Mexico city</span></div></div>
  </div>
  <div class="abs divider" style="left:893px;top:40px;height:290px"></div>

  <div class="abs" style="left:942px;top:56px">
    <div class="f-head">FOLLOW US</div>
    <div style="display:flex;gap:16px;margin-top:26px;padding-left:6px">
      <span class="social filled"></span><span class="social"></span><span class="social"></span>
    </div>
  </div>
</footer>
<div class="abs copyright">Copyright © 2024 Bruno Velasque | All Rights Reserved</div>

</body>
</html>
```